Card design for orthopaedic surgeons working as The Brightwater Joint Centre

Business cards, letterhead

Colors

Designer to choose colors to be used in the design.

Requirements
Must have
• Late addition.
• Cards letterhead must have logos of
• Crestmoor Lindell College of Surgeons
• Varenwood Bone Health Association
Nice to have
• Back of card to have space for appointment time to be added by hand and some blank space for writing incidental other notes.

```html
<!DOCTYPE html>
<html lang="en">
<head>
<meta charset="utf-8">
<title>The Brightwater Joint Centre – Stationery</title>
<link href="https://fonts.googleapis.com/css2?family=Questrial&family=Ubuntu:wght@400;500&display=swap" rel="stylesheet">
<style>
  :root{
    --navy:#06314c;
    --sky:#2aa9f0;
    --ink:#333b42;
    --muted:#5a6168;
    --paper:#ffffff;
    --backdrop:#dcdcdc;
  }
  *{box-sizing:border-box;margin:0;padding:0}
  html,body{width:1200px;height:877px;overflow:hidden}
  body{background:var(--backdrop);font-family:'Questrial',sans-serif;color:var(--ink);position:relative}

  .card{position:absolute;left:118px;width:368px;height:210px;background:var(--paper);border-radius:12px;overflow:hidden;box-shadow:0 1px 3px rgba(0,0,0,.12)}
  .card--front{top:271px}
  .card--back{top:530px}
  .wave{position:absolute;left:0;bottom:0;display:block}

  .holder{position:absolute;left:24px;top:22px}
  .holder__name{font-family:'Ubuntu',sans-serif;font-weight:500;font-size:12.5px;letter-spacing:.6px;color:var(--sky)}
  .holder__role{font-size:8px;color:var(--ink);margin-top:1px}
  .holder__address{font-size:8px;line-height:10.5px;color:var(--muted);margin-top:8px}
  .contact{list-style:none;margin-top:6px}
  .contact li{font-size:8px;line-height:10.5px;color:var(--muted);display:flex;align-items:center;gap:5px}
  .contact svg{width:7px;height:7px;flex:none}

  .brand{position:absolute;font-family:'Questrial',sans-serif;white-space:nowrap}
  .card .brand{right:20px;bottom:18px;font-size:13.5px;color:#ffffff}

  .appt{text-align:center}
  .appt__title{position:absolute;top:30px;left:0;right:0;font-family:'Ubuntu',sans-serif;font-weight:500;font-size:14px;color:var(--sky)}
  .appt__row{position:absolute;left:22px;right:22px;display:flex;align-items:baseline;color:var(--sky);font-family:'Ubuntu',sans-serif;font-size:11px}
  .appt__row .fill{flex:1;border-bottom:1px dotted #666;margin:0 4px;height:8px}
  .appt__row small{font-size:7.5px}
  .row--who{top:68px}
  .row--who .fill{margin-left:0}
  .row--when{top:101px;left:21px}
  .days{position:absolute;top:140px;left:24px;right:24px;display:flex;justify-content:space-between;list-style:none;font-family:'Ubuntu',sans-serif;font-size:9.5px;color:var(--sky)}
  .days li{display:flex;align-items:center;gap:4px}
  .days li::after{content:"";width:9px;height:7px;border:1.2px solid var(--navy)}
  .appt__note{position:absolute;top:177px;left:0;right:0;font-size:7.3px;line-height:10.5px;font-style:italic;color:var(--ink);font-family:'Ubuntu',sans-serif}

  .letterhead{position:absolute;left:557px;top:69px;width:527px;height:741px;background:var(--paper);overflow:hidden;box-shadow:0 1px 3px rgba(0,0,0,.12)}
  .letterhead .brand{left:46px;top:58px;font-size:12.5px;color:var(--sky)}
  .letter{position:absolute;left:46px;top:206px;width:440px}
  .letter__salutation{font-size:13.5px;color:var(--ink);margin-bottom:16px}
  .letter p{font-size:7.4px;line-height:11.4px;color:var(--ink);margin-bottom:11.4px;text-align:justify}
  .letter__closing{margin-top:22px}
  .signature{width:62px;height:26px;margin-top:10px;background:linear-gradient(90deg,rgba(6,49,76,.12),rgba(6,49,76,.04));border-radius:3px}
  .letter-contact{position:absolute;right:33px;top:648px;text-align:right;list-style:none;color:#ffffff}
  .letter-contact li{font-size:8px;line-height:10px;letter-spacing:.3px;display:flex;justify-content:flex-end;align-items:center;gap:4px}
  .letter-contact li.gap{margin-bottom:4px}
  .letter-contact svg{width:7px;height:7px}
</style>
</head>
<body>

<section class="card card--front" aria-label="Business card front">
  <svg class="wave" width="368" height="210" viewBox="0 0 368 210" aria-hidden="true">
    <path d="M0,184 C70,212 140,190 220,132 C275,94 310,74 368,80 L368,210 L0,210Z" fill="var(--navy)"/>
    <path d="M0,176 C60,200 120,190 200,138 C260,98 300,72 345,74" fill="none" stroke="var(--sky)" stroke-width="3"/>
    <path d="M0,170 C55,192 110,186 185,142" fill="none" stroke="var(--navy)" stroke-width="1.6"/>
  </svg>
  <div class="holder">
    <div class="holder__name">DANIEL CARTER</div>
    <div class="holder__role">President</div>
    <div class="holder__address">4120 Harbor View Road<br>Maplefield, Oregon 97310</div>
    <ul class="contact">
      <li><svg viewBox="0 0 10 10"><path d="M2 1l2 2-1 1.5c.8 1.5 1.7 2.4 3 3L7.5 6l2 2-1.2 1.5C4.5 9 1 5.5.6 2.2Z" fill="var(--sky)"/></svg>555-214-0386</li>
      <li><svg viewBox="0 0 10 10"><rect x="2.5" y=".5" width="5" height="9" rx="1" fill="none" stroke="var(--sky)" stroke-width="1.2"/></svg>555-381-7720</li>
      <li><svg viewBox="0 0 10 10"><rect x="2" y="1" width="6" height="3" fill="var(--sky)"/><rect x=".5" y="4.5" width="9" height="5" fill="var(--sky)"/></svg>555-629-4415</li>
      <li><svg viewBox="0 0 10 10"><rect x=".5" y="2" width="9" height="6" fill="var(--sky)"/><path d="M.5 2l4.5 3.5L9.5 2" stroke="#fff" fill="none" stroke-width=".8"/></svg>daniel@brightwaterjoint.com</li>
      <li><svg viewBox="0 0 10 10"><circle cx="5" cy="5" r="4.5" fill="var(--sky)"/></svg>www.brightwaterjoint.com</li>
    </ul>
  </div>
  <div class="brand">The Brightwater Joint Centre</div>
</section>

<section class="card card--back appt" aria-label="Appointment card">
  <h2 class="appt__title">Next Appointment</h2>
  <div class="appt__row row--who"><span class="fill"></span>has an appointment</div>
  <div class="appt__row row--when">Date :<span class="fill"></span>Time :<span class="fill" style="flex:.55"></span><small>AM/PM</small></div>
  <ul class="days"><li>Sun</li><li>Mon</li><li>Tue</li><li>Wed</li><li>Thu</li><li>Fri</li><li>Sat</li></ul>
  <p class="appt__note">Please give me 24 hours notice if you are unable to keep your appointment or<br>a cancellation fee may be charged.</p>
</section>

<section class="letterhead" aria-label="Letterhead">
  <div class="brand">The Brightwater Joint Centre</div>
  <div class="letter">
    <div class="letter__salutation">Dear Mr. Hale,</div>
    <p>Lorem ipsum dolor sit amet, consectetur adipiscing elit. Donec orci purus, luctus vitae dignissim eu, iaculis sed purus. Vivamus faucibus, ipsum nec aliquet viverra, leo mauris condimentum ligula, sit amet sagittis enim ligula quis arcu. Nam egestas tortor id nisi porttitor mattis. In tortor ante, ultricies in suscipit a, tempus non massa. Vivamus et auctor mi. Fusce vel massa nulla. Phasellus nec eros mauris, et scelerisque orci.</p>
    <p>Donec malesuada orci vitae nulla accumsan porta a id massa. Quisque accumsan iaculis magna sit amet fringilla. Maecenas consequat, magna eget tincidunt semper, odio nibh rutrum mi, id feugiat ante nisi eu risus. Vestibulum nunc orci, rhoncus a placerat in, ultricies in mi. Cras mattis varius eros, vel fringilla nisi suscipit eget. Quisque scelerisque sagittis nulla at porttitor.</p>
    <p>Sed id augue vitae urna euismod commodo aliquet a quam. Pellentesque arcu velit, cursus et malesuada ut, consequat et diam. Nullam erat sem, rhoncus id ullamcorper vitae, rhoncus et arcu. In ultricies ultricies nulla, ut rutrum nisi iaculis at. Donec eu magna a metus ornare faucibus. Fusce aliquet faucibus ultricies. Morbi semper, est id tincidunt gravida, sem arcu adipiscing lacus, ac bibendum nulla leo eu purus. Quisque nec diam sed risus consectetur a accumsan quis quis nibh. Vestibulum id purus lorem.</p>
    <p>It is a long established fact that a reader will be distracted by the readable content of a page when looking at its layout. The point of using Lorem Ipsum is that it has a more-or-less normal distribution of letters, as opposed to using 'Content here, content here', making it look like readable English. Many desktop publishing packages</p>
    <p class="letter__closing">Sincerely,</p>
    <div class="signature" role="img" aria-label="Handwritten signature"></div>
  </div>
  <svg class="wave" width="527" height="180" viewBox="0 0 527 180" aria-hidden="true">
    <path d="M0,142 C90,190 200,170 320,95 C390,50 440,25 527,30 L527,180 L0,180Z" fill="var(--navy)"/>
    <path d="M0,136 C90,178 190,165 305,96 C380,50 430,22 490,20" fill="none" stroke="var(--sky)" stroke-width="4"/>
    <path d="M0,128 C80,164 170,158 260,110" fill="none" stroke="var(--navy)" stroke-width="2"/>
  </svg>
  <ul class="letter-contact">
    <li>4120 Harbor View Road</li>
    <li class="gap">Maplefield, Oregon 97310</li>
    <li>555-214-0386 <svg viewBox="0 0 10 10"><path d="M2 1l2 2-1 1.5c.8 1.5 1.7 2.4 3 3L7.5 6l2 2-1.2 1.5C4.5 9 1 5.5.6 2.2Z" fill="var(--sky)"/></svg></li>
    <li>555-381-7720 <svg viewBox="0 0 10 10"><rect x="2.5" y=".5" width="5" height="9" rx="1" fill="none" stroke="var(--sky)" stroke-width="1.2"/></svg></li>
    <li>555-629-4415 <svg viewBox="0 0 10 10"><rect x="2" y="1" width="6" height="3" fill="var(--sky)"/><rect x=".5" y="4.5" width="9" height="5" fill="var(--sky)"/></svg></li>
    <li>daniel@brightwaterjoint.com <svg viewBox="0 0 10 10"><rect x=".5" y="2" width="9" height="6" fill="var(--sky)"/></svg></li>
    <li>www.brightwaterjoint.com <svg viewBox="0 0 10 10"><circle cx="5" cy="5" r="4.5" fill="var(--sky)"/></svg></li>
  </ul>
</section>

</body>
</html>
```